A resume/portfolio website for myself

I'm an independent software contractor, architect, tech trainer. I need a web site to present myself. Many ready to use portfolio designs are too artistic and focused on presenting design skills of the person. I like a nice website but the content should be a little less graphic than if you would present a graphic designer. Content could be presentation of me, core skill qualities and services and resume. Potentially a page with my tech courses in the longer run

```html
<!DOCTYPE html>
<html lang="en">
<head>
<meta charset="utf-8">
<title>Anders Vinter – Software Contractor</title>
<link href="https://fonts.googleapis.com/css2?family=Roboto:wght@400;500;700&display=swap" rel="stylesheet">
<style>
:root{
  --navy:#2d5286;
  --navy-dark:#0d2a66;
  --orange:#fda61a;
  --grey-bg:#efefef;
  --card-bg:#f0f0f0;
  --card-border:#9fb1c9;
  --text:#777;
  --heading:#1e1e1e;
  --white:#fff;
}
*{box-sizing:border-box;margin:0;padding:0}
html,body{width:1200px;height:3593px;overflow:hidden}
body{position:relative;font-family:'Roboto',Arial,sans-serif;background:var(--white);color:var(--text)}
.abs{position:absolute}

/* Header */
.top-band{left:0;top:0;width:1200px;height:170px;background:linear-gradient(90deg,#1f4f9c 0%,#27508f 55%,#223d66 100%)}
.social-top{top:29px;left:112px;display:flex;gap:26px}
.social-top span{width:37px;height:37px;border:2px solid var(--white);border-radius:50%;color:var(--white);font-size:8px;display:flex;align-items:center;justify-content:center;font-weight:500}
.btn-resume{left:876px;top:29px;width:212px;height:55px;background:var(--orange);color:var(--white);font-weight:700;font-size:14px;display:flex;align-items:center;justify-content:center}

/* Hero */
.hero{left:0;top:170px;width:1200px;height:514px;background:linear-gradient(135deg,#f5f5f5,#e9e9e9 50%,#f3f3f3);border-bottom:4px solid var(--navy)}
.name-box{left:432px;top:135px;width:335px;height:70px;background:var(--white);color:var(--navy);font-size:35px;font-weight:700;display:flex;align-items:center;justify-content:center}
.portrait{left:152px;top:217px;width:404px;height:404px;border-radius:50%;border:6px solid var(--navy);background:radial-gradient(circle at 50% 40%,#cfcfcf,#8a8a8a 60%,#3a3a3a)}
.intro-title{left:598px;top:240px;width:458px;color:var(--navy);font-size:21px;font-weight:700;white-space:nowrap;padding-bottom:8px;border-bottom:2px solid var(--navy);overflow:visible}
.intro-text{left:598px;top:292px;width:475px;font-size:13.5px;line-height:25.8px}
.intro-text p+p{margin-top:26px}

/* Work */
.section-title{left:0;width:1200px;text-align:center;font-weight:700;font-size:35px}
.work-title{top:765px;color:var(--navy)}
.job-card{width:664px;height:175px;background:var(--card-bg);border:1px solid var(--card-border);border-radius:10px;padding:16px 28px 0 38px}
.job-card h3{color:var(--navy);font-size:18px;font-weight:500;margin-bottom:10px;margin-left:3px}
.job-card p{font-size:13px;line-height:25.8px}
.job-date{width:182px;height:182px;border-radius:50%;background:var(--navy);border:3px solid var(--white);box-shadow:0 0 0 2px var(--navy);color:var(--white);display:flex;flex-direction:column;align-items:center;justify-content:center;text-align:center}
.job-date b{font-size:17px;font-weight:500;line-height:26px}
.job-date small{font-size:13px;margin-top:10px}
.connector{height:2px;background:var(--navy)}
.dot{width:17px;height:17px;border-radius:50%;background:var(--navy)}

/* Education */
.edu{left:112px;top:2236px;width:976px;height:204px;background:linear-gradient(120deg,#0c2a6e,#102c6c 60%,#0a1f55);overflow:hidden}
.edu-photo{left:0;top:0;width:480px;height:204px;background:linear-gradient(180deg,#9cb96f,#6f8c4c 50%,#5f7443);clip-path:polygon(0 0,468px 0,400px 100%,0 100%)}
.edu-stripe{left:0;top:0;width:490px;height:204px;background:var(--white);clip-path:polygon(468px 0,480px 0,412px 100%,400px 100%)}
.edu-text{left:513px;top:44px;width:440px;color:var(--white)}
.edu-text h3{font-size:25px;font-weight:700}
.edu-text h4{color:var(--orange);font-size:18px;font-weight:700;margin:6px 0 12px}
.edu-text p{font-size:13.5px;line-height:26px}

/* Portfolio */
.portfolio{left:0;top:2535px;width:1200px;height:581px;background:linear-gradient(160deg,#2d79c9 0%,#3d9ee0 50%,#6fbde8 100%)}
.portfolio-title{top:2600px;color:var(--white)}
.work-card{top:2673px;width:310px;height:357px;background:var(--white);text-align:center}
.work-img{height:204px;width:100%}
.work-card h3{color:var(--heading);font-size:20px;font-weight:500;margin:30px 0 14px}
.work-card p{font-size:13.5px;line-height:26px;padding:0 20px}

/* Contact */
.contact-title{top:3173px;color:var(--heading)}
.contact-sub{left:0;top:3236px;width:1200px;text-align:center;color:var(--navy);font-size:18px;font-weight:500;white-space:nowrap}
.contact-text{left:180px;top:3277px;width:840px;text-align:center;font-size:13.5px;line-height:25.8px}
.social-bottom{left:468px;top:3435px;display:flex;gap:24px}
.social-bottom span{width:48px;height:48px;border-radius:50%;background:var(--navy);color:var(--white);font-size:8px;font-weight:500;display:flex;align-items:center;justify-content:center}
.copyright{left:0;top:3512px;width:1200px;text-align:center;font-size:13.5px}
</style>
</head>
<body>

<header>
  <div class="abs top-band"></div>
  <nav class="abs social-top" aria-label="Social profiles">
    <span>Folkly</span><span>Chirp</span><span>Grid+</span><span>Link</span><span>Pin</span>
  </nav>
  <div class="abs btn-resume">DOWNLOAD MY RESUME</div>
</header>

<section>
  <div class="abs hero"></div>
  <h1 class="abs name-box">ANDERS VINTER</h1>
  <div class="abs portrait" role="img" aria-label="Portrait photograph of Anders Vinter"></div>
  <h2 class="abs intro-title">I'M AN INDEPENDENT SOFTWARE CONTRACTOR</h2>
  <div class="abs intro-text">
    <p>Lorem ipsum dolor sit amet, consectetur adipiscing elit, sed do eiusmod tempor incididunt ut labore et dolore magna aliqua. Ut enim ad minim veniam, quis nostrud exercitation ullamco laboris nisi ut aliquip ex ea commodo consequat. Duis aute irure dolor in reprehenderit in voluptate velit esse cillum dolore eu fugiat nulla pariatur. Excepteur sint occaecat cupidatat non proident, sunt in culpa qui officia deserunt mollit anim id est laborum.</p>
    <p>Lorem ipsum dolor sit amet, consectetur adipiscing elit, sed do eiusmod tempor incididunt ut labore et dolore magna aliqua. Ut enim ad minim veniam, quis nostrud exercitation ullamco laboris nisi ut aliquip ex ea commodo consequat. Duis aute irure dolor in reprehenderit in voluptate velit esse cillum dolore eu fugiat nulla pariatur.</p>
  </div>
</section>

<section>
  <h2 class="abs section-title work-title">WORK EXPERIENCES</h2>

  <div class="abs job-date" style="left:152px;top:837px"><b>Lorem ipsum<br>dolor</b><small>Oct 2000,sep 2002</small></div>
  <div class="abs connector" style="left:337px;top:927px;width:48px"></div>
  <div class="abs dot" style="left:378px;top:919px"></div>
  <div class="abs job-card" style="left:381px;top:841px"><h3>Nemo enim ipsam voluptatem</h3><p>Lorem ipsum dolor sit amet, consectetur adipiscing elit, sed do eiusmod tempor incididunt ut labore et dolore magna aliqua. Ut enim ad minim veniam, quis nostrud exercitation ullamco laboris nisi ut aliquip ex ea commodo consequat. Duis aute irure dolor in reprehenderit in voluptate velit esse cillum dolore eu fugiat nulla pariatur. Excepteur sint occaecat</p></div>

  <div class="abs job-card" style="left:151px;top:1066px"><h3>Nemo enim ipsam voluptatem</h3><p>Lorem ipsum dolor sit amet, consectetur adipiscing elit, sed do eiusmod tempor incididunt ut labore et dolore magna aliqua. Ut enim ad minim veniam, quis nostrud exercitation ullamco laboris nisi ut aliquip ex ea commodo consequat. Duis aute irure dolor in reprehenderit in voluptate velit esse cillum dolore eu fugiat nulla pariatur. Excepteur sint occaecat</p></div>
  <div class="abs connector" style="left:812px;top:1152px;width:52px"></div>
  <div class="abs dot" style="left:801px;top:1144px"></div>
  <div class="abs job-date" style="left:862px;top:1062px"><b>Lorem ipsum<br>dolor</b><small>Oct 2000,sep 2002</small></div>

  <div class="abs job-date" style="left:152px;top:1287px"><b>Lorem ipsum<br>dolor</b><small>Oct 2000,sep 2002</small></div>
  <div class="abs connector" style="left:337px;top:1377px;width:48px"></div>
  <div class="abs dot" style="left:378px;top:1369px"></div>
  <div class="abs job-card" style="left:381px;top:1291px"><h3>Nemo enim ipsam voluptatem</h3><p>Lorem ipsum dolor sit amet, consectetur adipiscing elit, sed do eiusmod tempor incididunt ut labore et dolore magna aliqua. Ut enim ad minim veniam, quis nostrud exercitation ullamco laboris nisi ut aliquip ex ea commodo consequat. Duis aute irure dolor in reprehenderit in voluptate velit esse cillum dolore eu fugiat nulla pariatur. Excepteur sint occaecat</p></div>

  <div class="abs job-card" style="left:151px;top:1516px"><h3>Nemo enim ipsam voluptatem</h3><p>Lorem ipsum dolor sit amet, consectetur adipiscing elit, sed do eiusmod tempor incididunt ut labore et dolore magna aliqua. Ut enim ad minim veniam, quis nostrud exercitation ullamco laboris nisi ut aliquip ex ea commodo consequat. Duis aute irure dolor in reprehenderit in voluptate velit esse cillum dolore eu fugiat nulla pariatur. Excepteur sint occaecat</p></div>
  <div class="abs connector" style="left:812px;top:1602px;width:52px"></div>
  <div class="abs dot" style="left:801px;top:1594px"></div>
  <div class="abs job-date" style="left:862px;top:1512px"><b>Lorem ipsum<br>dolor</b><small>Oct 2000,sep 2002</small></div>

  <div class="abs job-date" style="left:152px;top:1737px"><b>Lorem ipsum<br>dolor</b><small>Oct 2000,sep 2002</small></div>
  <div class="abs connector" style="left:337px;top:1827px;width:48px"></div>
  <div class="abs dot" style="left:378px;top:1819px"></div>
  <div class="abs job-card" style="left:381px;top:1741px"><h3>Nemo enim ipsam voluptatem</h3><p>Lorem ipsum dolor sit amet, consectetur adipiscing elit, sed do eiusmod tempor incididunt ut labore et dolore magna aliqua. Ut enim ad minim veniam, quis nostrud exercitation ullamco laboris nisi ut aliquip ex ea commodo consequat. Duis aute irure dolor in reprehenderit in voluptate velit esse cillum dolore eu fugiat nulla pariatur. Excepteur sint occaecat</p></div>

  <div class="abs job-card" style="left:151px;top:1966px"><h3>Nemo enim ipsam voluptatem</h3><p>Lorem ipsum dolor sit amet, consectetur adipiscing elit, sed do eiusmod tempor incididunt ut labore et dolore magna aliqua. Ut enim ad minim veniam, quis nostrud exercitation ullamco laboris nisi ut aliquip ex ea commodo consequat. Duis aute irure dolor in reprehenderit in voluptate velit esse cillum dolore eu fugiat nulla pariatur. Excepteur sint occaecat</p></div>
  <div class="abs connector" style="left:812px;top:2052px;width:52px"></div>
  <div class="abs dot" style="left:801px;top:2044px"></div>
  <div class="abs job-date" style="left:862px;top:1962px"><b>Lorem ipsum<br>dolor</b><small>Oct 2000,sep 2002</small></div>
</section>

<section class="abs edu">
  <div class="abs edu-photo" role="img" aria-label="Photograph of a university building among trees"></div>
  <div class="abs edu-stripe"></div>
  <div class="abs edu-text">
    <h3>WORK EXPERIENCES</h3>
    <h4>Diploma in Software Engineering</h4>
    <p>Nordlys Tech Institute<br>2002 - 2005</p>
  </div>
</section>

<section>
  <div class="abs portfolio"></div>
  <h2 class="abs section-title portfolio-title">PORTFOLIO (JUST A SELECTION)</h2>
  <article class="abs work-card" style="left:112px">
    <div class="work-img" role="img" aria-label="Photo of colleagues smiling in an office" style="background:linear-gradient(135deg,#b8a58a,#6e5a48)"></div>
    <h3>SED UT PERSPICIATIS</h3>
    <p>Nemo enim ipsam voluptatem quia voluptas sit aspernatur aut odit aut fugit, sed quia consequuntur magni</p>
  </article>
  <article class="abs work-card" style="left:445px">
    <div class="work-img" role="img" aria-label="Group photo of a team" style="background:linear-gradient(180deg,#d9d4cc,#4a4f5c)"></div>
    <h3>SED UT PERSPICIATIS</h3>
    <p>Nemo enim ipsam voluptatem quia voluptas sit aspernatur aut odit aut fugit, sed quia consequuntur magni</p>
  </article>
  <article class="abs work-card" style="left:778px">
    <div class="work-img" role="img" aria-label="Black and white portrait photo" style="background:linear-gradient(180deg,#bdbdbd,#6a6a6a)"></div>
    <h3>SED UT PERSPICIATIS</h3>
    <p>Nemo enim ipsam voluptatem quia voluptas sit aspernatur aut odit aut fugit, sed quia consequuntur magni</p>
  </article>
</section>

<footer>
  <h2 class="abs section-title contact-title">GET IN TOUCH</h2>
  <p class="abs contact-sub">I'M AN INDEPENDENT SOFTWARE CONTRACTOR, ARCHITECT, TECH TRAINER.</p>
  <p class="abs contact-text">Sed ut perspiciatis unde omnis iste natus error sit voluptatem accusantium doloremque laudantium, totam rem aperiam, eaque ipsa quae ab illo inventore veritatis et quasi architecto beatae vitae dicta sunt explicabo. Nemo enim ipsam voluptatem quia voluptas sit aspernatur aut odit aut fugit, sed quia consequuntur magni dolores eos qui ratione voluptatem sequi nesciunt. Neque porro quisquam est, qui dolorem ipsum quia dolor sit amet, consectetur, adipisci velit, sed quia non numquam eius modi tempora incidunt ut labore et dolore magnam aliquam quaerat voluptatem.</p>
  <nav class="abs social-bottom" aria-label="Social channels">
    <span>Folkly</span><span>Chirp</span><span>Vidflow</span><span>Snap</span>
  </nav>
  <p class="abs copyright">© Copyrights 2020 Company name | All Rights Reserved</p>
</footer>

</body>
</html>
```